R7M Horizon Business Card Design

We need a business card created for our New Business "R7M Horizon"<br/><br/>The business card design is up to you however the following information must be on the business card:<br/><br/>Front of the business card -<br/>Email :darrenp@r7mhorizon.nz<br/>Mobile: +64 (0) 22 4870 619<br/>Website: www.r7mhorizon.nz<br/>Card Owner Name: Darren Paltrow<br/>Company Title: Business Development Manager<br/>Slogan: "The BEST of both worlds". <br/>Logo On the front attached to the design brief<br/><br/>On the back: <br/>Space on the back for 4 more versions of the logo across the bottom of the card indicating different subsidiary brands - R7M Coffee, R7M Arts, R7M ?? (The card will be used for all of these brands - We Will add the extra subsidiary logos to the design once the design is finished (We are a graphics design team). <br/><br/>Other than that we want a premium feeling logo that remains universally usable depending on the business entity that we are using the card for. The use of bright bold colours would be great but we still want the card to feel premium.
Target Market(s)
Gift Design and Manufacturing Companies
Contact Information for Business Card
Front of the business card -
Email :darrenp@r7mhorizon.nz
Mobile: +64 (0) 22 4870 619
Website: www.r7mhorizon.nz
Card Owner Name: Darren Paltrow
Company Title: Business Development Manager
Slogan: "The BEST of both worlds".
Logo On the front attached to the design brief

```html
<!DOCTYPE html>
<html lang="en">
<head>
<meta charset="utf-8">
<title>R7M Horizon Business Card</title>
<link href="https://fonts.googleapis.com/css2?family=Titillium+Web:wght@400;600&display=swap" rel="stylesheet">
<style>
  :root {
    --bg: #e9e6e1;
    --card: #23262d;
    --card-edge: #1c1f25;
    --blue: #4750a8;
    --blue-dim: #2f3778;
    --ring: #2a3050;
    --emboss: #3b3e46;
    --white: #f2f2f4;
    --icon: #3d4590;
  }
  * { box-sizing: border-box; margin: 0; padding: 0; }
  html, body { width: 1200px; height: 859px; overflow: hidden; }
  body {
    background: var(--bg);
    font-family: "Titillium Web", sans-serif;
    position: relative;
  }
  .card {
    position: absolute;
    top: 288px;
    width: 500px;
    height: 285px;
    background: var(--card);
    border-radius: 11px;
    overflow: hidden;
    box-shadow: 0 10px 24px rgba(0,0,0,0.28);
  }
  .card--front { left: 60px; }
  .card--back { left: 640px; }
  .card__stripes { position: absolute; inset: 0; }
  .brand-name {
    position: absolute;
    left: 23px;
    top: 24px;
    color: var(--blue);
    font-weight: 600;
    font-size: 31px;
    letter-spacing: 0.5px;
    line-height: 1;
  }
  .owner {
    position: absolute;
    left: 23px;
    top: 130px;
  }
  .owner__bar {
    position: absolute;
    left: -23px;
    top: 3px;
    width: 6px;
    height: 30px;
    background: var(--blue);
  }
  .owner__name {
    color: var(--blue);
    font-weight: 600;
    font-size: 18px;
    line-height: 1;
    text-transform: uppercase;
    letter-spacing: 0.2px;
  }
  .owner__title {
    color: var(--white);
    font-size: 13px;
    line-height: 1;
    margin-top: 5px;
    letter-spacing: -0.2px;
  }
  .contacts {
    position: absolute;
    left: 23px;
    top: 186px;
    list-style: none;
  }
  .contacts__item {
    display: flex;
    align-items: center;
    gap: 7px;
    color: var(--white);
    font-size: 13px;
    line-height: 17px;
    letter-spacing: 0.3px;
  }
  .contacts__item svg { width: 12px; height: 12px; flex: none; }
  .slogan {
    position: absolute;
    left: 23px;
    top: 247px;
    color: var(--blue-dim);
    font-size: 13px;
    line-height: 1;
  }
  .back-mark {
    position: absolute;
    left: 0; right: 0;
    top: 120px;
    text-align: center;
    color: var(--emboss);
    font-weight: 600;
    font-size: 36px;
    letter-spacing: 1px;
    line-height: 1;
    text-shadow: none;
  }
</style>
</head>
<body>

<section class="card card--front" aria-label="Card front">
  <svg class="card__stripes" viewBox="0 0 500 285" aria-hidden="true">
    <polygon points="500,69 500,141 362,285 286,285" fill="var(--blue)"/>
    <polygon points="500,221 500,285 437,285" fill="var(--blue)"/>
  </svg>

  <div class="brand-name">R7M Horizon</div>

  <div class="owner">
    <span class="owner__bar"></span>
    <p class="owner__name">Darren Paltrow</p>
    <p class="owner__title">Business Development Manager</p>
  </div>

  <ul class="contacts">
    <li class="contacts__item">
      <svg viewBox="0 0 12 12" aria-hidden="true"><circle cx="6" cy="6" r="5" fill="none" stroke="var(--icon)" stroke-width="1.2"/><path d="M4 3.5 l1.2 1.3 -0.6 0.8 1.8 1.8 0.8 -0.6 1.3 1.2 -0.8 0.9 c-2 0 -4.5 -2.5 -4.5 -4.5z" fill="var(--icon)"/></svg>
      +64 (0) 22 4870 619
    </li>
    <li class="contacts__item">
      <svg viewBox="0 0 12 12" aria-hidden="true"><rect x="1" y="2.5" width="10" height="7" fill="none" stroke="var(--icon)" stroke-width="1.2"/><path d="M1 2.5 L6 6.5 L11 2.5" fill="none" stroke="var(--icon)" stroke-width="1.2"/></svg>
      darrenp@r7mhorizon.nz
    </li>
    <li class="contacts__item">
      <svg viewBox="0 0 12 12" aria-hidden="true"><circle cx="6" cy="6" r="5" fill="none" stroke="var(--icon)" stroke-width="1.2"/><path d="M1 6 H11 M6 1 C3.5 3.5 3.5 8.5 6 11 M6 1 C8.5 3.5 8.5 8.5 6 11" fill="none" stroke="var(--icon)" stroke-width="1"/></svg>
      www.r7mhorizon.nz
    </li>
  </ul>

  <p class="slogan">The BEST of both worlds</p>
</section>

<section class="card card--back" aria-label="Card back">
  <svg class="card__stripes" viewBox="0 0 500 285" aria-hidden="true">
    <polygon points="66,0 142,0 0,142 0,64" fill="var(--blue)"/>
    <circle cx="256" cy="141" r="142" fill="none" stroke="var(--ring)" stroke-width="2"/>
  </svg>
  <div class="back-mark">R7M Horizon</div>
</section>

</body>
</html>
```